Create a banner for me that embodies my health and well being package.

I am an intuitive counselor with a busy practice helping clients to shift their blocks and move forward in their lives.
I have created a package called '9 paths home again'
I am wanting a banner to put on my website page, facebook page and to use as a letter head in mailouts.
My ideal clients are those who want to create change in their lives and who invest money in themselves and their personal and spiritual growth.
I am different to regular life coaches as my sessions have a spiritual twist to them creating much deeper change in my clients.
I would like the banner to be mainly font with the title of the progam: 9 Paths Home Again (no other wording) (something along the lines of the Blackjack font) and that ties in with the theme of my website. I'm not sure what else I want with it and am looking for ideas.
Website:
www.lumorawellspring.com.au
I also have a current facebook page for the business:
https://www.facebook.com/Lumora-Wellspring-Studio-502718364091557/
(Note: I am about to drop my logo and business name and move to using my own name - the rest of the website will remain the same).
I have attached a doc with the draft of what wording will be on the website page any advertising will link to, to give you an idea of what the program is about.

Target Market(s)

People who invest money on themselves who are looking to improve their emotional well being and creating change in their life. Majority are middle aged women (also younger females and some men)

Industry/Entity Type

Health And Wellness

Font styles to use
Other font styles liked:
• I like Blackjack and Amienne. Along those lines.

Requirements
Must have
• Attractive, modern and GREAT font.
Nice to have
• Surprise me with something amazing!
• I love the colours in the 2 images I have up loaded as they represent the heart chakra colours. They could be a feature on the banner or blurred into the background.
Should not have
• Even though my work is quite spiritual I don't want it to look woo woo (meaning airy fairy spiritual stuff!)

```html
<!DOCTYPE html>
<html lang="en">
<head>
<meta charset="utf-8">
<title>9 Paths Home Again — Lumora Wellspring</title>
<link href="https://fonts.googleapis.com/css2?family=Great+Vibes&family=Oswald:wght@500&family=Playfair+Display:wght@900&family=Quicksand:wght@500&display=swap" rel="stylesheet">
<style>
  :root {
    --purple: #5a16c4;
    --sage: #4f7153;
    --paper: #ffffff;
    --leaf-light: #e9efd6;
    --leaf: #b9cf8a;
    --leaf-deep: #8fae5c;
    --skin: #eac3a6;
    --disc: #e9e9e9;
    --brand: #6b8f6e;
  }
  html, body {
    margin: 0;
    padding: 0;
    width: 1200px;
    height: 444px;
    overflow: hidden;
    background: var(--paper);
  }
  .banner {
    position: relative;
    width: 1200px;
    height: 444px;
    overflow: hidden;
  }
  .backdrop {
    position: absolute;
    inset: 0;
    background:
      radial-gradient(ellipse 190px 240px at 940px 170px, var(--skin) 0%, rgba(234,195,166,0.6) 45%, rgba(234,195,166,0) 75%),
      radial-gradient(ellipse 260px 300px at 900px 200px, rgba(215,166,111,0.75) 0%, rgba(215,166,111,0) 80%),
      radial-gradient(ellipse 420px 260px at 420px 160px, var(--leaf) 0%, rgba(185,207,138,0) 80%),
      radial-gradient(ellipse 300px 220px at 1150px 120px, var(--leaf-deep) 0%, rgba(143,174,92,0) 80%),
      linear-gradient(90deg, var(--leaf-light) 0%, #d7e3b4 40%, #c9da9c 70%, #b6cc84 100%);
  }
  .paper, .tagline {
    position: absolute;
    left: 0;
    top: 0;
  }
  .ornament {
    position: absolute;
    background: rgba(255,255,255,0.35);
    border-radius: 50%;
  }
  .ornament--left { left: 40px; top: 230px; width: 170px; height: 150px; }
  .ornament--right { right: 0; top: 110px; width: 110px; height: 170px; }
  .brand {
    position: absolute;
    left: 544px;
    top: 0;
    width: 120px;
    height: 120px;
    background: var(--paper);
    display: flex;
    flex-direction: column;
    align-items: center;
    justify-content: center;
    gap: 8px;
    box-shadow: 0 1px 3px rgba(0,0,0,0.08);
  }
  .brand__dot {
    width: 44px;
    height: 44px;
    border-radius: 50%;
    background: #cfe0cf;
  }
  .brand__name {
    font-family: "Quicksand", sans-serif;
    font-weight: 500;
    font-size: 13px;
    line-height: 1.1;
    text-align: center;
    color: var(--brand);
  }
  .numeral-disc {
    position: absolute;
    left: 70px;
    top: 86px;
    width: 176px;
    height: 176px;
    border-radius: 50%;
    background: radial-gradient(circle at 40% 35%, #fafafa 0%, var(--disc) 70%, #dcdcdc 100%);
  }
  .title {
    position: absolute;
    left: 158px;
    top: 86px;
    margin: 0;
    display: flex;
    align-items: baseline;
    color: var(--purple);
    font-weight: normal;
    white-space: nowrap;
  }
  .title__number {
    font-family: "Playfair Display", serif;
    font-weight: 900;
    font-size: 190px;
    line-height: 1;
  }
  .title__words {
    font-family: "Great Vibes", cursive;
    font-size: 132px;
    line-height: 1;
    margin-left: 4px;
  }
  .tagline__text {
    font-family: "Oswald", sans-serif;
    font-weight: 500;
    font-size: 42px;
    fill: var(--sage);
  }
</style>
</head>
<body>
<div class="banner">
  <div class="backdrop" role="img" aria-label="Soft-focus green garden photograph with a smiling young woman tilting her head back in sunlight"></div>

  <svg class="paper" width="1200" height="444" viewBox="0 0 1200 444" aria-hidden="true">
    <path fill="#ffffff" opacity="0.85"
      d="M0 0 H250 L238 18 L246 34 L226 52 L232 70 L205 88 L190 104 L150 112 L110 108 L70 120 L30 116 L0 124 Z"/>
    <path fill="#ffffff"
      d="M0 444 V300 L60 296 L120 304 L190 298 L260 306 L330 300 L400 296 L460 290
         L520 292 L580 286 L640 290 L700 300 L760 308 L820 312 L880 318 L940 314
         L1000 322 L1060 330 L1120 336 L1160 334 L1200 340 V444 Z"/>
  </svg>

  <div class="ornament ornament--left" role="img" aria-label="Pale floral flourish"></div>
  <div class="ornament ornament--right" role="img" aria-label="Pale swirling leaf flourish"></div>

  <div class="brand">
    <span class="brand__dot"></span>
    <span class="brand__name">Lumora<br>Wellspring</span>
  </div>

  <div class="numeral-disc"></div>

  <h1 class="title">
    <span class="title__number">9</span>
    <span class="title__words">Paths home again</span>
  </h1>

  <svg class="tagline" width="1200" height="444" viewBox="0 0 1200 444">
    <text class="tagline__text" x="418" y="358" textLength="700" lengthAdjust="spacingAndGlyphs">DISCOVER THE INFINIT RESOURCES WITHIN YOU</text>
  </svg>
</div>
</body>
</html>
```